Wordpress Design Project - Australian Solar Company wants to start FRESH!

About us

Bright Meadow are a renewable energy company based in Perth Australia, but we also have offices all over Asia. We specialise in offering renewable energy solutions (Solar PV Systems and LED Lighting) to residential and commercial customers.

Our current website: www.brightmeadowenergy.com.au

Our needs

This will be a replacement website as we are not happy with our current layout. We have an Australian company doing our SEO and they have recommended a new layout which we wish to go with.

We really want a professional and easy to navigate website that will assist in bringing in more enquiries and phone calls.

Content

We have all the content and will get the design winner to add this after we have chosen the design we like.
It is important that the call to actions are presented well and are visible these are things like the free quote form and our phone number.

The layout as we have advised has been based on SEO research so we wish it to be exactly the same unless otherwise stated.

Call to action

Our main objective of the new website is for people to come to the home page and see us as a professional and reliable company to deal with and enquire further.

We really want as many people as we can to convert to a lead. We want every person that comes to the website to enquire online or call us. We feel it is important to have a contact us/quote form on every page of the website.

Functional requirements

We have a chatterbook and vidstream account so links to these would be needed

Design assets

The logo needs to be displayed as shown in the website layout brief

Colours – we would like fresh, subdued colours that are professional and appealing to the eye. We ask that you do not take the colours from the logo.

Current website dislikes – the things we currently dislike about our current website is that it is hard to find information and there is no clear call to action. The colours are really unappealing as well as it looks cheap not professional.
The graphics that we require for the slider on the home page will have to be given after the winner is chosen but we want there to be three sliders on rotation

- Credibility builder (employee infront of solar panel) that encourages we use all our own employees not subcontractors
- Residential Slider – picture of a couple and solar panel system with a testimonial
- Commercial slider – picture of commercial system with “find out how you can install solar for free* at your business”

Design ideas

The website needs to be mobile friendly as well
It is going to be a total rebuild from the current website as our current website really isn’t working for us.

Target Market(s)

Target Audience

Our target audience are both residential and commercial clients
Residential – we want to attract home owners that are interested in reducing their electricity bill and helping the environment. Generally these people are between the ages of 28-50+ both male and female.

Commercial – We want to appeal to key decision makers within the commercial sphere. For example – CEOs, Company Directors, Operation managers and business owners of any industry. These people will be interested in reducing their electricity bills and creating a clean green image for their business.
Our target audience will generally come to our website to get information and enquire for a quote/ product information.

Industry/Entity Type

Residential

Requirements
Must have
• MUST BE LAID OUT LIKE THIS:

http://www.pagevaultdocs.com/doc/482937105/Website-Layout

Must have Enquire Now forms on every page that read:

Name
Phone Number
How did you hear about us
Message

```html
<!DOCTYPE html>
<html lang="en">
<head>
<meta charset="utf-8">
<title>Bright Meadow – Home</title>
<link href="https://fonts.googleapis.com/css2?family=Source+Sans+3:wght@400;600;700&display=swap" rel="stylesheet">
<style>
:root{
  --sun:#fbb829;
  --leaf:#1a8a3c;
  --leaf-dark:#0f7a32;
  --ink:#555;
  --ink-soft:#6b6b6b;
  --ink-dark:#333;
  --field:#f1f1f1;
  --night:#2d2d2d;
  --white:#fff;
  --social:#3b5a9a;
}
*{box-sizing:border-box;margin:0;padding:0}
html,body{width:890px;height:1200px;overflow:hidden;background:var(--white)}
body{position:relative;font-family:"Source Sans 3",Arial,sans-serif;color:var(--ink)}
a{text-decoration:none}
.abs{position:absolute}

/* header */
.brand{left:68px;top:50px;font-size:30px;font-weight:600;color:var(--ink-dark);line-height:1}
.call{left:588px;top:34px;font-size:18px;font-weight:600;color:var(--sun);display:flex;align-items:center;gap:6px}
.social{left:788px;top:28px;width:36px;height:36px;border-radius:50%;background:var(--social)}
.nav{left:346px;top:84px;width:478px;height:36px;background:var(--sun);border-radius:3px;display:flex;align-items:center;justify-content:space-around;padding:0 6px}
.nav a{color:var(--white);font-size:12px;font-weight:600}
.nav a.current{color:var(--leaf)}

/* hero */
.hero{left:0;top:134px;width:890px;height:330px;background:linear-gradient(180deg,#8fb8e0 0%,#cfe2f2 22%,#6f86c2 35%,#3d54a6 55%,#7dbb3c 72%,#4f9a25 100%)}
.hero-caption{left:0;top:256px;width:366px;height:101px;background:rgba(40,45,60,.72);clip-path:polygon(0 0,100% 0,78% 100%,0 100%)}
.hero-caption p{position:absolute;left:84px;top:12px;font-size:20px;font-weight:600;color:var(--white);line-height:22px}
.dots{left:414px;top:441px;display:flex;gap:5px}
.dots span{width:13px;height:13px;border-radius:50%;background:var(--white)}

.quote{left:600px;top:150px;width:224px;height:298px;background:rgba(255,255,255,.55);border:1px solid rgba(255,255,255,.8);border-radius:3px}
.quote-title{position:absolute;left:12px;top:10px;display:flex;align-items:center;gap:8px;font-size:18px;font-weight:600;color:var(--leaf)}
.quote-rule{position:absolute;left:12px;right:12px;top:46px;border-top:1px solid rgba(255,255,255,.9)}
.field{position:absolute;left:12px;width:201px;height:29px;background:var(--white);border:1px solid #ddd;font-size:10px;color:#777;padding:7px 12px}
.field.tall{height:61px}
.field-label{position:absolute;left:12px;top:139px;font-size:10px;color:#555}
.caret{position:absolute;right:10px;top:12px;border:5px solid transparent;border-top:6px solid #888}
.btn{position:absolute;background:var(--sun);color:var(--white);font-weight:600;text-align:center;border-radius:2px}
.quote .btn{left:76px;top:264px;width:86px;height:26px;line-height:26px;font-size:13px}

/* services */
.service{top:480px;width:178px}
.service h2{font-size:17px;font-weight:600;color:var(--leaf);white-space:nowrap}
.service .photo{margin-top:8px;width:173px;height:127px;border:1px solid #ddd;padding:3px;background:var(--white);box-shadow:0 1px 2px rgba(0,0,0,.1)}
.service .photo div{width:100%;height:100%}
.service p{margin:14px 0 0 6px;font-size:10.5px;line-height:17px;color:var(--ink-soft);text-align:justify;width:164px}
.service .btn{position:static;display:block;margin:5px 0 0 6px;width:86px;height:26px;line-height:26px;font-size:14px}

/* welcome */
.welcome{left:69px;top:770px;width:494px}
.welcome h2,.testimonials h2{font-size:17px;font-weight:600;color:var(--leaf)}
.welcome p{margin-top:8px;font-size:10.5px;line-height:17px;color:var(--ink-soft);text-align:justify}
.testimonials{left:590px;top:770px}
.video{left:588px;top:805px;width:236px;height:131px;background:linear-gradient(120deg,#6b6b62,#3b4036 60%,#5a6a55);border-radius:2px}
.play{left:681px;top:846px;width:48px;height:48px;border-radius:50%;background:rgba(220,220,220,.75)}
.play::after{content:"";position:absolute;left:20px;top:15px;border:9px solid transparent;border-left:12px solid #333;border-right:0}

/* footer */
.footer{left:0;top:969px;width:890px;height:193px;background:var(--sun);border-top:2px solid #e9a817}
.foot-head{top:984px;font-size:13px;font-weight:400;color:#444}
.foot-list{left:68px;top:1014px;list-style:none}
.foot-list li{font-size:9.5px;color:#333;line-height:21.6px}
.foot-list li::before{content:"•";margin-right:6px}
.badge{width:52px;height:31px;background:var(--white);border-radius:1px}
.foot-field{position:absolute;left:436px;width:146px;height:25px;background:var(--field);border-radius:2px;font-size:8.5px;color:#444;padding:7px 12px}
.submit{left:479px;top:1129px;width:64px;height:19px;line-height:19px;background:var(--leaf-dark);color:var(--white);font-size:9.5px;font-weight:700;text-align:center;border-radius:1px}
.contact-icon{width:26px;height:26px;border-radius:50%;background:#eee;display:flex;align-items:center;justify-content:center}
.contact-text{font-size:9.5px;line-height:15.5px;color:#333}
.bottom{left:0;top:1162px;width:890px;height:38px;background:var(--night);color:#bbb;font-size:10px;text-align:center;line-height:38px}
</style>
</head>
<body>

<header>
  <div class="abs brand">Bright Meadow</div>
  <div class="abs call">
    <svg width="16" height="14" viewBox="0 0 24 24"><path fill="#fbb829" d="M6.6 10.8a15 15 0 0 0 6.6 6.6l2.2-2.2c.3-.3.7-.4 1-.2 1.1.4 2.3.6 3.6.6.6 0 1 .4 1 1V20c0 .6-.4 1-1 1A17 17 0 0 1 3 4c0-.6.4-1 1-1h3.5c.6 0 1 .4 1 1 0 1.3.2 2.5.6 3.6.1.3 0 .7-.2 1z"/></svg>
    Call us : 1800 472 9063
  </div>
  <a class="abs social" href="#" aria-label="chatterbook"></a>
  <nav class="abs nav">
    <a class="current" href="#">Home</a><a href="#">About Us</a><a href="#">Products</a><a href="#">Services</a><a href="#">Why Bright Meadow</a><a href="#">Contact Us</a>
  </nav>
</header>

<section>
  <div class="abs hero" role="img" aria-label="Rows of blue solar panels on a green grass field under a cloudy sky"></div>
  <div class="abs hero-caption"><p>Lorem ipsum dolor sit amet,<br>consectetur adipisicing<br>elit, sed do eiusmod</p></div>
  <div class="abs dots"><span></span><span></span><span></span><span></span></div>

  <form class="abs quote">
    <div class="quote-title">
      <svg width="28" height="28" viewBox="0 0 28 28"><rect x="4" y="3" width="18" height="22" fill="#fff" stroke="#888"/><path d="M8 9h10M8 13h10M8 17h7" stroke="#999"/><path d="M14 22 25 8l2 2-11 14-3 1z" fill="#f2a81c"/></svg>
      Get a Free Quote
    </div>
    <div class="quote-rule"></div>
    <div class="field" style="top:60px">Name</div>
    <div class="field" style="top:99px">Phone Number</div>
    <div class="field-label">How did you hear about us?</div>
    <div class="field" style="top:157px">Online<span class="caret"></span></div>
    <div class="field tall" style="top:195px">Message</div>
    <div class="btn">Get a Quote</div>
  </form>
</section>

<section>
  <article class="abs service" style="left:68px">
    <h2>Residential Solar Power</h2>
    <div class="photo"><div role="img" aria-label="Two installers fitting solar panels on a house roof" style="background:linear-gradient(180deg,#7fa9d8,#3e5c8a 55%,#3a3f4a)"></div></div>
    <p>Donec sagittis interdum metus nec semper. Vivamus hendrerit ipsum massa</p>
    <a class="btn" href="#">Read more</a>
  </article>
  <article class="abs service" style="left:262px">
    <h2>Commercial Solar Power</h2>
    <div class="photo"><div role="img" aria-label="Close view of solar panels against a blue sky" style="background:linear-gradient(135deg,#6fb0e8,#2559a8 60%,#1c3f7a)"></div></div>
    <p>Donec sagittis interdum metus nec semper. Vivamus hendrerit ipsum massa</p>
    <a class="btn" href="#">Read more</a>
  </article>
  <article class="abs service" style="left:456px">
    <h2>Air Conditioning WA</h2>
    <div class="photo"><div role="img" aria-label="Technicians servicing an outdoor air conditioning unit" style="background:linear-gradient(135deg,#c9c2b6,#8a7f72 50%,#5b534c)"></div></div>
    <p>Donec sagittis interdum metus nec semper. Vivamus hendrerit ipsum massa</p>
    <a class="btn" href="#">Read more</a>
  </article>
  <article class="abs service" style="left:651px">
    <h2>LED Lighting</h2>
    <div class="photo"><div role="img" aria-label="LED street light module on a white background" style="background:radial-gradient(circle,#d6d9dc,#f4f4f4 70%)"></div></div>
    <p>Donec sagittis interdum metus nec semper. Vivamus hendrerit ipsum massa</p>
    <a class="btn" href="#">Read more</a>
  </article>
</section>

<section>
  <div class="abs welcome">
    <h2>Welcome to Bright Meadow</h2>
    <p>Nunc at elementum nulla, sed sollicitudin enim. Suspendisse venenatis, magna sed volutpat vehicula, libero tortor tempus erat, scelerisque tempus nulla velit lacinia nisi. Maecenas fermentum mauris luctus facilisis consequat. Aliquam erat volutpat. Duis a posuere est.</p>
    <p>Fusce non vulputate odio. Maecenas in nibh id nulla tempus varius vehicula lacinia neque. Aliquam erat volutpat. Sed non fermentum justo, sed scelerisque neque. Sed arcu justo, ullamcorper et enim et, tincidunt dictum justo. Aliquam consectetur libero eu rutrum blandit. Pellentesque quis imperdiet ligula. Nulla velit nibh, lacinia eu magna eu, ultrices luctus urna. Integer augue est, sollicitudin non erat a, suscipit lacinia nibh. Suspendisse sit amet massa venenatis, suscipit risus sit amet, aliquet diam.</p>
  </div>
  <div class="abs testimonials"><h2>Testimonials</h2></div>
  <div class="abs video" role="img" aria-label="Video still of a customer in a bright modern home"></div>
  <div class="abs play" aria-label="Play video"></div>
</section>

<footer>
  <div class="abs footer"></div>
  <h3 class="abs foot-head" style="left:68px">Primary Products</h3>
  <ul class="abs foot-list">
    <li>Integer lobortis</li><li>Curabitur ac malesuada</li><li>Phasellus tellus nisl</li><li>Aenean fringilla</li><li>Vestibulum venenatis nibh nec</li><li>Aliquam commodo</li>
  </ul>

  <h3 class="abs foot-head" style="left:246px">Memberships</h3>
  <div class="abs badge" style="left:247px;top:1017px" role="img" aria-label="Member badge"></div>
  <div class="abs badge" style="left:309px;top:1017px" role="img" aria-label="Member badge"></div>
  <div class="abs badge" style="left:247px;top:1055px" role="img" aria-label="Member badge"></div>
  <div class="abs badge" style="left:309px;top:1055px" role="img" aria-label="Member badge"></div>
  <div class="abs badge" style="left:247px;top:1094px" role="img" aria-label="Member badge"></div>
  <div class="abs badge" style="left:309px;top:1094px" role="img" aria-label="Member badge"></div>

  <h3 class="abs foot-head" style="left:438px">Request Quotation</h3>
  <div class="foot-field" style="top:1011px">Name</div>
  <div class="foot-field" style="top:1040px">Phone</div>
  <div class="foot-field" style="top:1069px">How did you know about us?</div>
  <div class="foot-field" style="top:1098px">Message</div>
  <div class="abs submit">Submit</div>

  <h3 class="abs foot-head" style="left:668px">Contact us</h3>
  <div class="abs contact-icon" style="left:668px;top:1015px">
    <svg width="14" height="14" viewBox="0 0 24 24"><path fill="#999" d="M6.6 10.8a15 15 0 0 0 6.6 6.6l2.2-2.2c.3-.3.7-.4 1-.2 1.1.4 2.3.6 3.6.6.6 0 1 .4 1 1V20c0 .6-.4 1-1 1A17 17 0 0 1 3 4c0-.6.4-1 1-1h3.5c.6 0 1 .4 1 1 0 1.3.2 2.5.6 3.6.1.3 0 .7-.2 1z"/></svg>
  </div>
  <div class="abs contact-text" style="left:703px;top:1013px">1300 574 219<br>(08) 6397 4182</div>
  <div class="abs contact-icon" style="left:668px;top:1052px">
    <svg width="14" height="12" viewBox="0 0 24 18"><rect x="1" y="1" width="22" height="16" fill="#999"/><path d="M1 1l11 9 11-9" fill="none" stroke="#eee" stroke-width="2"/></svg>
  </div>
  <div class="abs contact-text" style="left:703px;top:1057px">sales@brightmeadowenergy.com.au</div>
  <div class="abs contact-icon" style="left:668px;top:1091px">
    <svg width="14" height="14" viewBox="0 0 24 24"><path fill="#999" d="M12 3 2 12h3v9h5v-6h4v6h5v-9h3z"/></svg>
  </div>
  <div class="abs contact-text" style="left:703px;top:1090px">Glenmore Plaza, 42 Wattle<br>Street Glenmore WA 6071<br>Perth, Western Australia 6082</div>

  <div class="abs bottom">Copyright © 2013 Bright Meadow. All rights reserved.</div>
</footer>

</body>
</html>
```